Brewlark Cup Society - A Monthly Subscription Coffee Club - Shopify Website Design

A monthly subscription company. Need a Shopify Website Design and uploaded to fully work with Tidal Renewals.

Please look at these sites for examples as well as the images I enclosed.

https://www.sipvantor.com/
https://mokrate.com/
https://www.platewinder.com/
https://www.globunchies.com/

Number of Pages Required

1 page

```html
<!DOCTYPE html>
<html lang="en">
<head>
<meta charset="utf-8">
<title>Brewlark Cup Society</title>
<link href="https://fonts.googleapis.com/css2?family=Rye&family=Montserrat:wght@400;500;600;700&display=swap" rel="stylesheet">
<style>
:root{
  --cream:#f8e8c8;
  --card:#f4dfba;
  --ink:#2b1d14;
  --muted:#5d4a3b;
  --accent:#c4571d;
  --bar:#3a2418;
  --sale:#e6175c;
  --line:#d9c3a0;
  --white:#ffffff;
}
*{box-sizing:border-box;margin:0;padding:0}
html,body{width:1200px;height:3220px;overflow:hidden;background:var(--cream)}
body{font-family:'Montserrat',sans-serif;color:var(--ink);position:relative}
.abs{position:absolute}
.announce{left:0;top:0;width:1200px;height:20px;background:var(--bar);color:var(--white);font-size:10px;text-align:center;line-height:20px}
.search{left:144px;top:64px;font-size:12px;color:var(--muted);display:flex;align-items:center;gap:8px}
.brand{left:0;width:1200px;top:56px;text-align:center;font-family:'Rye',serif;font-size:28px;letter-spacing:1px;color:var(--ink)}
.icons{left:1012px;top:62px;display:flex;gap:14px}
.nav{left:0;width:1200px;top:156px;display:flex;justify-content:center;gap:36px;font-size:11px;font-weight:600;letter-spacing:.5px}
.nav a{color:var(--ink);text-decoration:none;padding-bottom:6px}
.nav a.active{border-bottom:2px solid var(--ink)}
.rule{left:144px;width:912px;height:1px;background:var(--line)}
.hero{left:144px;top:232px;width:912px;height:468px;background:linear-gradient(120deg,#1c130e 0%,#2e1d13 45%,#5a3520 75%,#3a2417 100%)}
.hero-title{left:144px;width:912px;top:368px;text-align:center;font-family:'Rye',serif;font-size:46px;color:#e9dccb;letter-spacing:2px}
.hero-sub{left:144px;width:912px;top:446px;text-align:center;font-size:14px;color:#efe3d2}
.btn{background:var(--accent);color:var(--white);font-size:11px;font-weight:700;letter-spacing:.5px;text-align:center}
.hero-btn{left:538px;top:506px;width:124px;height:38px;line-height:38px}
.arrow{top:454px}
.intro{left:190px;width:820px;top:768px;text-align:center;font-size:13px;line-height:24px;color:var(--muted)}
.product-img{width:280px;height:312px}
.p-name{width:280px;text-align:center;font-size:14px;font-weight:700;letter-spacing:.5px}
.p-price{width:280px;text-align:center;font-size:13px;color:var(--accent);font-weight:600}
.sale{width:56px;height:56px;border-radius:50%;background:var(--sale);color:var(--white);font-size:11px;font-weight:700;text-align:center;line-height:14px;padding-top:14px}
.post-date{width:444px;text-align:center;font-size:10px;color:var(--muted);letter-spacing:.5px}
.post-title{width:444px;text-align:center;font-size:15px;font-weight:700;letter-spacing:.5px}
.post-img{width:444px;height:404px}
.post-text{width:444px;font-size:13px;line-height:20px;color:var(--ink)}
.read{font-size:12px;color:var(--accent);text-decoration:underline}
.news-title{left:0;width:1200px;top:2578px;text-align:center;font-family:'Rye',serif;font-size:36px;letter-spacing:2px;color:var(--muted)}
.news-sub{left:0;width:1200px;top:2640px;text-align:center;font-size:13px;color:var(--muted)}
.news-input{left:360px;top:2708px;width:370px;height:44px;background:var(--white);font-size:12px;color:var(--muted);padding:14px 16px}
.news-btn{left:730px;top:2708px;width:102px;height:44px;line-height:44px}
.f-head{top:2898px;font-size:14px;font-weight:700;letter-spacing:1px}
.f-links{top:2940px;font-size:12px;line-height:22px;list-style:none}
.social{left:184px;top:2940px;display:flex;gap:14px}
.social span{width:16px;height:16px;border-radius:50%;background:var(--ink);display:block}
.f-about{left:668px;top:2940px;width:320px;font-size:12px;line-height:20px}
.copy{left:0;width:1200px;top:3152px;text-align:center;font-size:11px;color:var(--ink)}
</style>
</head>
<body>
<div class="abs announce">Local Saturday delivery is now open. Please order before Friday at 5:00pm to join in.</div>

<div class="abs search">
  <svg width="12" height="12" viewBox="0 0 12 12"><circle cx="5" cy="5" r="4" fill="none" stroke="#2b1d14" stroke-width="1.4"/><line x1="8" y1="8" x2="11" y2="11" stroke="#2b1d14" stroke-width="1.4"/></svg>
  Search
</div>
<div class="abs brand">Brewlark Cup Society</div>
<div class="abs icons">
  <svg width="18" height="18" viewBox="0 0 18 18"><circle cx="9" cy="9" r="8" fill="none" stroke="#2b1d14" stroke-width="1.4"/><circle cx="9" cy="7" r="3" fill="none" stroke="#2b1d14" stroke-width="1.4"/><path d="M3.5 14.5c2-3 9-3 11 0" fill="none" stroke="#2b1d14" stroke-width="1.4"/></svg>
  <svg width="16" height="18" viewBox="0 0 16 18"><rect x="1.5" y="5" width="13" height="12" fill="none" stroke="#2b1d14" stroke-width="1.4"/><path d="M5 5V3.5a3 3 0 0 1 6 0V5" fill="none" stroke="#2b1d14" stroke-width="1.4"/></svg>
</div>
<nav class="abs nav">
  <a class="active">HOME</a><a>SHOP ▾</a><a>SUBSCRIPTION</a><a>ABOUT US</a><a>CONTACT</a>
</nav>
<div class="abs rule" style="top:190px"></div>

<div class="abs hero" role="img" aria-label="Dark photo of roasted coffee beans in a wooden tray"></div>
<div class="abs hero-title">BREWLARK CUP SOCIETY</div>
<div class="abs hero-sub">Lorem ipsum dolor sit amet, consectetur adipiscing elit</div>
<div class="abs btn hero-btn">SIGN UP NOW</div>
<svg class="abs arrow" style="left:150px" width="14" height="18" viewBox="0 0 14 18"><path d="M10 2L3 9l7 7" fill="none" stroke="#fff" stroke-width="2.4"/></svg>
<svg class="abs arrow" style="left:1036px" width="14" height="18" viewBox="0 0 14 18"><path d="M4 2l7 7-7 7" fill="none" stroke="#fff" stroke-width="2.4"/></svg>

<div class="abs rule" style="top:740px"></div>
<p class="abs intro">Lorem ipsum dolor sit amet, consectetur adipiscing elit, sed do eiusmod tempor incididunt ut labore et dolore magna aliqua ipsum suspendisse ultrices commodo viverra maecenas accumsan lacus vel facilisis lorem ipsum dolor sit amet consectetur adipiscing elit sed do eiusmod tempor incididunt ut labore et dolore magna aliqua ipsum suspendisse ultrices commodo viverra maecenas accumsan lacus vel facilisis.</p>
<div class="abs rule" style="top:928px"></div>

<!-- products row 1 -->
<div class="abs product-img" style="left:144px;top:996px;background:radial-gradient(circle at 50% 50%,#4a2a18 0%,#6b4128 38%,var(--card) 40%)" role="img" aria-label="Two bags of coffee beans"></div>
<div class="abs product-img" style="left:460px;top:996px;background:radial-gradient(ellipse at 50% 55%,#c99a62 0%,#8a5a34 35%,var(--card) 42%)" role="img" aria-label="Wooden gift box filled with coffee beans"></div>
<div class="abs sale" style="left:472px;top:1024px">SAVE<br>$10</div>
<div class="abs product-img" style="left:776px;top:996px;background:radial-gradient(ellipse at 50% 50%,#b98a58 0%,#8d6a3f 36%,var(--card) 42%)" role="img" aria-label="Open cardboard box with coffee beans"></div>
<div class="abs p-name" style="left:144px;top:1332px">PRODUCT NAME</div>
<div class="abs p-name" style="left:460px;top:1332px">PRODUCT NAME</div>
<div class="abs p-name" style="left:776px;top:1332px">PRODUCT NAME</div>
<div class="abs p-price" style="left:144px;top:1362px">$50.67</div>
<div class="abs p-price" style="left:460px;top:1362px">$50.67</div>
<div class="abs p-price" style="left:776px;top:1362px">$50.67</div>

<!-- products row 2 -->
<div class="abs product-img" style="left:144px;top:1412px;background:radial-gradient(ellipse at 50% 55%,#d9a86e 0%,#b27c48 36%,var(--card) 42%)" role="img" aria-label="Empty open cardboard box"></div>
<div class="abs product-img" style="left:460px;top:1412px;background:radial-gradient(ellipse at 50% 55%,#2b1a12 0%,#5a3a24 34%,var(--card) 42%)" role="img" aria-label="Scattered coffee beans beside a small wooden crate"></div>
<div class="abs sale" style="left:472px;top:1440px">SAVE<br>$10</div>
<div class="abs product-img" style="left:776px;top:1412px;background:radial-gradient(ellipse at 50% 50%,#5a3020 0%,#a87a4c 36%,var(--card) 42%)" role="img" aria-label="Open box of coffee beans"></div>
<div class="abs p-name" style="left:144px;top:1752px">PRODUCT NAME</div>
<div class="abs p-name" style="left:460px;top:1752px">PRODUCT NAME</div>
<div class="abs p-name" style="left:776px;top:1752px">PRODUCT NAME</div>
<div class="abs p-price" style="left:144px;top:1780px">$50.67</div>
<div class="abs p-price" style="left:460px;top:1780px">$50.67</div>
<div class="abs p-price" style="left:776px;top:1780px">$50.67</div>

<!-- blog posts -->
<div class="abs post-date" style="left:144px;top:1830px">AUGUST 07, 2020</div>
<div class="abs post-date" style="left:612px;top:1830px">AUGUST 07, 2020</div>
<div class="abs post-title" style="left:144px;top:1852px">SED UT PERSPICIATIS UNDEOM</div>
<div class="abs post-title" style="left:612px;top:1852px">SED UT PERSPICIATIS UNDEOM</div>
<div class="abs post-img" style="left:144px;top:1896px;background:linear-gradient(135deg,#3a3a3a,#6e6e6e 50%,#2c2c2c)" role="img" aria-label="Black and white photo of coffee beans in a grid of compartments"></div>
<div class="abs post-img" style="left:612px;top:1896px;background:linear-gradient(135deg,#4a4a4a,#262626 50%,#5a5a5a)" role="img" aria-label="Black and white photo of a tray full of coffee beans"></div>
<p class="abs post-text" style="left:144px;top:2318px">Lorem ipsum dolor sit amet, consectetur adipiscing elit, sed do eiusmod tempor incididunt ut labore et dolore magna aliqua. Quis ipsum suspendisse ultrices gravida.</p>
<p class="abs post-text" style="left:612px;top:2318px">Lorem ipsum dolor sit amet, consectetur adipiscing elit, sed do eiusmod tempor incididunt ut labore et dolore magna aliqua. Quis ipsum suspendisse ultrices gravida.</p>
<div class="abs read" style="left:144px;top:2416px">READ MORE</div>
<div class="abs read" style="left:612px;top:2416px">READ MORE</div>

<div class="abs rule" style="top:2500px"></div>
<div class="abs news-title">SUBSCRIBE TO OUR NEWSLETTER</div>
<div class="abs news-sub">Sign up to our Newsletter to receive updates about our future mailer!</div>
<div class="abs news-input">Enter Email</div>
<div class="abs btn news-btn">SUBSCRIBE</div>
<div class="abs rule" style="top:2840px"></div>

<!-- footer -->
<div class="abs f-head" style="left:184px">SOCIAL</div>
<div class="abs social"><span></span><span></span><span></span><span></span></div>
<div class="abs f-head" style="left:444px">NAVIGATE</div>
<ul class="abs f-links" style="left:444px"><li>Home</li><li>Shop</li><li>Subscription</li><li>About Us</li><li>Contact</li></ul>
<div class="abs f-head" style="left:668px">ABOUT US</div>
<p class="abs f-about">Lorem ipsum dolor sit amet, consectetur adipiscing elit, sed do eiusmod tempor incididunt ut labore et dolore magna aliqua. Quis ipsum suspendisse ultrices gravida. Risus commodo viverra maecenas accumsan lacus vel facilisis.</p>
<div class="abs rule" style="top:3116px"></div>
<div class="abs copy">© 2020 Brewlark Cup Society All Rights Reserved &nbsp;|&nbsp; Privacy Policy &nbsp;|&nbsp; Terms and Use</div>
</body>
</html>
```